Tech Company New PowerPoint Design Project

We are an IT Managed services, cloud and cyber security company https://www.travolin.com.au/ Requesting proposals for a PowerPoint deck template that can be used by our sales team when pitching clients, our head office is located in Australa and we do have regional offices in NZ , USA , SRI LANKA and SINGAPORE. and also required to have a proposal/SOW template created too (not sure if this is something that we can include to this proposal) we may need a lot of things done in future but this is where i like to get started for now.. please let m eknow your thoughts and if you have any questions.
Target Market(s)
Enterprise
Industry/Entity Type
Information Technology
Look and feel

```html
<!DOCTYPE html>
<html lang="en">
<head>
<meta charset="utf-8">
<title>Travolin – Sales Deck</title>
<link href="https://fonts.googleapis.com/css2?family=Roboto:wght@300;400;500;700&display=swap" rel="stylesheet">
<style>
:root{
  --blue:#35b8e8;
  --blue-light:#4cc9f0;
  --grey:#5f646b;
  --grey-dark:#4f545a;
  --text:#333a40;
  --muted:#7a7f85;
  --pale:#d6f1fb;
  --page:#ffffff;
}
*{box-sizing:border-box;margin:0;padding:0}
html,body{width:1200px;height:4051px;overflow:hidden;background:var(--page)}
body{position:relative;font-family:'Roboto',Arial,sans-serif;color:var(--text)}
.slide{position:absolute;left:75px;width:1048px;height:588px;background:#fff;overflow:hidden;box-shadow:0 6px 22px rgba(40,60,80,.14)}
.logo{position:absolute;left:60px;top:34px;font-family:'Roboto',Arial,sans-serif;font-weight:300;font-size:50px;letter-spacing:2px;color:var(--blue);line-height:1}
.logo.light{color:#fff}
.header-band{position:absolute;left:0;top:0;width:1048px;height:82px}
.slide-title{position:absolute;right:58px;top:25px;font-size:28px;font-weight:700;color:#fff;letter-spacing:.5px}
.slide-intro{position:absolute;left:60px;width:928px;text-align:center;font-size:13px;line-height:22px;color:var(--text)}
.slide-footer{position:absolute;left:0;top:538px;width:1048px;height:44px;background:linear-gradient(90deg,var(--grey) 0%,#5d8fa5 45%,var(--blue) 100%)}
.slide-footer .url{position:absolute;left:60px;top:14px;font-size:13px;color:#fff}
.slide-footer .sep{position:absolute;left:238px;top:12px;width:1px;height:20px;background:rgba(255,255,255,.7)}
.social{position:absolute;top:11px;width:22px;height:22px;border-radius:50%;background:#fff}
.page-no{position:absolute;right:58px;top:4px;width:36px;height:36px;border-radius:50%;background:#fff;border:2px solid var(--blue);text-align:center;line-height:32px;font-size:14px;font-weight:700;color:var(--text)}

/* slide 1 */
.cover{background:linear-gradient(150deg,var(--grey) 0%,#5a7e92 40%,var(--blue) 100%)}
.cover .welcome{position:absolute;left:60px;top:192px;font-size:16px;color:#fff;letter-spacing:.5px}
.cover h1{position:absolute;left:58px;top:214px;font-size:58px;font-weight:700;color:#fff;letter-spacing:1px}
.cover .lead{position:absolute;left:60px;top:296px;width:450px;font-size:16.5px;line-height:26px;color:#fff;font-weight:300}
.cover .photo{position:absolute;left:0;top:0}

/* slide 2 */
.about-frame{position:absolute;left:61px;top:138px;width:430px;height:324px;background:var(--pale)}
.about-photo{position:absolute;left:83px;top:158px;width:430px;height:326px;background:linear-gradient(135deg,#b9a894 0%,#7d8a8f 45%,#d8d4cc 100%)}
.about-text{position:absolute;left:546px;top:150px;width:442px}
.about-text .lead{font-size:12.5px;line-height:22px;color:var(--text);text-align:justify;margin-bottom:12px}
.about-text ul{list-style:none}
.about-text li{position:relative;padding-left:28px;font-size:11px;line-height:18px;color:var(--muted);text-align:justify;margin-bottom:10px}
.about-text li svg{position:absolute;left:0;top:3px;width:12px;height:12px}

/* slide 3 */
.offer-grid{position:absolute;left:63px;top:184px;display:grid;grid-template-columns:repeat(4,218px);grid-auto-rows:66px;column-gap:17px;row-gap:21px}
.offer-card{display:flex;align-items:center;gap:14px;background:#fff;box-shadow:0 2px 10px rgba(40,60,80,.16);padding:0 8px 0 6px}
.icon-tile{flex:none;width:54px;height:54px;background:linear-gradient(135deg,var(--grey) 0%,var(--blue) 100%);display:flex;align-items:center;justify-content:center}
.icon-tile svg{width:30px;height:30px}
.offer-card span{font-size:11px;line-height:16px;font-weight:500;color:var(--text);text-transform:uppercase}

/* slide 4 */
.desk-diagram{position:absolute;left:0;top:0}
.desk-item{position:absolute;left:517px;width:420px}
.desk-item h3{font-size:12px;font-weight:700;color:var(--text);margin-bottom:6px}
.desk-item p{font-size:10.5px;line-height:16px;color:var(--muted)}

/* slide 5 */
.dev-card{position:absolute;top:179px;width:288px;height:283px;background:#fff;box-shadow:0 2px 14px rgba(40,60,80,.15);text-align:center;padding:28px 20px 0}
.dev-icon{width:70px;height:70px;border-radius:50%;margin:0 auto 24px;background:linear-gradient(135deg,var(--grey) 0%,var(--blue) 100%);display:flex;align-items:center;justify-content:center}
.dev-icon svg{width:34px;height:34px}
.dev-card h3{font-size:14px;line-height:21px;font-weight:500;color:var(--text);margin-bottom:12px;text-transform:uppercase}
.dev-card p{font-size:11.5px;line-height:20px;color:var(--muted)}

/* slide 6 */
.contact{background:linear-gradient(150deg,var(--grey) 0%,#5e8aa0 45%,var(--blue) 100%)}
.contact .title-band{position:absolute;left:0;top:0}
.contact .slide-title{color:#4a4f55}
.contact-card{position:absolute;width:283px;height:152px;border:1.5px solid rgba(255,255,255,.55);border-radius:4px;text-align:center;color:#fff;padding:34px 12px 0}
.contact-card.main{background:#fff;color:var(--text);border-color:#fff}
.contact-card .pin{position:absolute;left:122px;top:-19px;width:38px;height:38px;border-radius:50%;background:var(--blue);border:2px solid #fff;display:flex;align-items:center;justify-content:center}
.contact-card .pin svg{width:16px;height:16px}
.contact-card h4{font-size:13px;font-weight:500;margin-bottom:8px;text-transform:uppercase}
.contact-card p{font-size:9px;line-height:14px;margin-bottom:6px}
.contact-card .line{font-size:9.5px;line-height:16px}
.contact-card .line svg{width:9px;height:9px;vertical-align:-1px;margin-right:6px}
.contact .slide-footer{background:#fff}
.contact .slide-footer .url{color:var(--text)}
.contact .slide-footer .sep{background:var(--muted)}
.contact .social{background:var(--grey)}
.contact .page-no{background:var(--grey);border-color:var(--blue);color:#fff}
</style>
</head>
<body>

<svg width="0" height="0" style="position:absolute">
  <defs>
    <linearGradient id="band-grad" x1="0" x2="1" y1="0" y2="0">
      <stop offset="0" stop-color="#5f646b"/>
      <stop offset=".35" stop-color="#5f646b"/>
      <stop offset=".62" stop-color="#35b8e8"/>
      <stop offset="1" stop-color="#35b8e8"/>
    </linearGradient>
    <linearGradient id="disc-grad" x1="0" x2="1" y1="0" y2="1">
      <stop offset="0" stop-color="#5f646b"/>
      <stop offset="1" stop-color="#35b8e8"/>
    </linearGradient>
    <linearGradient id="portrait-grad" x1="0" x2="1" y1="0" y2="1">
      <stop offset="0" stop-color="#e9ecee"/>
      <stop offset=".55" stop-color="#c9ced2"/>
      <stop offset="1" stop-color="#8d9aa3"/>
    </linearGradient>
    <symbol id="i-shield" viewBox="0 0 24 24"><path d="M12 3l7 3v5c0 5-3 8-7 10-4-2-7-5-7-10V6z" fill="none" stroke="#fff" stroke-width="1.6"/><path d="M9 12l2 2 4-4" fill="none" stroke="#fff" stroke-width="1.6"/></symbol>
    <symbol id="i-server" viewBox="0 0 24 24"><rect x="4" y="4" width="16" height="6" fill="none" stroke="#fff" stroke-width="1.6"/><rect x="4" y="14" width="16" height="6" fill="none" stroke="#fff" stroke-width="1.6"/><circle cx="7" cy="7" r="1" fill="#fff"/><circle cx="7" cy="17" r="1" fill="#fff"/></symbol>
    <symbol id="i-gear" viewBox="0 0 24 24"><circle cx="12" cy="12" r="3.5" fill="none" stroke="#fff" stroke-width="1.6"/><path d="M12 3v3M12 18v3M3 12h3M18 12h3M5.6 5.6l2.1 2.1M16.3 16.3l2.1 2.1M5.6 18.4l2.1-2.1M16.3 7.7l2.1-2.1" stroke="#fff" stroke-width="1.8"/></symbol>
    <symbol id="i-lock" viewBox="0 0 24 24"><rect x="5" y="11" width="14" height="10" fill="none" stroke="#fff" stroke-width="1.6"/><path d="M8 11V8a4 4 0 018 0v3" fill="none" stroke="#fff" stroke-width="1.6"/></symbol>
    <symbol id="i-db" viewBox="0 0 24 24"><ellipse cx="12" cy="6" rx="7" ry="2.5" fill="none" stroke="#fff" stroke-width="1.6"/><path d="M5 6v12c0 1.4 3.1 2.5 7 2.5s7-1.1 7-2.5V6M5 12c0 1.4 3.1 2.5 7 2.5s7-1.1 7-2.5" fill="none" stroke="#fff" stroke-width="1.6"/></symbol>
    <symbol id="i-cloud" viewBox="0 0 24 24"><path d="M7 18h10a4 4 0 000-8 5 5 0 00-9.6-1A4.5 4.5 0 007 18z" fill="none" stroke="#fff" stroke-width="1.6"/></symbol>
    <symbol id="i-code" viewBox="0 0 24 24"><rect x="3" y="4" width="18" height="14" fill="none" stroke="#fff" stroke-width="1.6"/><path d="M9 9l-3 2 3 2M15 9l3 2-3 2" fill="none" stroke="#fff" stroke-width="1.6"/></symbol>
    <symbol id="i-monitor" viewBox="0 0 24 24"><rect x="3" y="4" width="18" height="12" fill="none" stroke="#fff" stroke-width="1.6"/><path d="M9 20h6M12 16v4" stroke="#fff" stroke-width="1.6"/></symbol>
    <symbol id="i-chart" viewBox="0 0 24 24"><path d="M4 20h16M7 17v-6M11 17V7M15 17v-4M19 17V9" stroke="#fff" stroke-width="2"/></symbol>
    <symbol id="i-globe" viewBox="0 0 24 24"><circle cx="12" cy="12" r="8" fill="none" stroke="#fff" stroke-width="1.6"/><path d="M4 12h16M12 4c3 3 3 13 0 16M12 4c-3 3-3 13 0 16" fill="none" stroke="#fff" stroke-width="1.4"/></symbol>
    <symbol id="i-cart" viewBox="0 0 24 24"><path d="M3 5h3l2 10h10l2-7H7" fill="none" stroke="#fff" stroke-width="1.6"/><circle cx="10" cy="19" r="1.5" fill="#fff"/><circle cx="17" cy="19" r="1.5" fill="#fff"/></symbol>
    <symbol id="i-pin" viewBox="0 0 24 24"><path d="M12 22s7-7 7-12a7 7 0 00-14 0c0 5 7 12 7 12z" fill="#fff"/><circle cx="12" cy="10" r="2.5" fill="#35b8e8"/></symbol>
    <symbol id="i-phone" viewBox="0 0 24 24"><path d="M6 3l4 1 1 5-2 2a12 12 0 005 5l2-2 5 1 1 4-3 2C10 21 3 14 3 6z" fill="currentColor"/></symbol>
    <symbol id="i-mail" viewBox="0 0 24 24"><rect x="2" y="5" width="20" height="14" fill="currentColor"/><path d="M2 5l10 8 10-8" fill="none" stroke="#fff" stroke-width="1.5"/></symbol>
    <symbol id="i-check" viewBox="0 0 24 24"><rect x="3" y="3" width="18" height="18" fill="none" stroke="#35b8e8" stroke-width="2"/><path d="M7 12l4 4 9-10" fill="none" stroke="#35b8e8" stroke-width="2.4"/></symbol>
  </defs>
</svg>

<!-- Slide 1: Cover -->
<section class="slide cover" style="top:88px">
  <svg class="photo" width="1048" height="588" viewBox="0 0 1048 588">
    <circle cx="915" cy="148" r="392" fill="#fff"/>
    <circle cx="915" cy="148" r="382" fill="url(#portrait-grad)" role="img" aria-label="Photo of a smiling woman with glasses working at a laptop on a desk"/>
  </svg>
  <div class="logo light">travolin</div>
  <div class="welcome">WELCOME TO</div>
  <h1>TRAVOLIN</h1>
  <p class="lead">TRAVOLIN is a one-stop destination for all your IT Management Requirements. We are committed to delivering cutting-edge, simplified IT solutions through our highly skilled team and flexible engagement models.</p>
</section>

<!-- Slide 2: About Us -->
<section class="slide" style="top:745px">
  <svg class="header-band" viewBox="0 0 1048 82"><polygon points="346,0 1048,0 1048,82 428,82" fill="url(#band-grad)"/></svg>
  <div class="logo">travolin</div>
  <div class="slide-title">ABOUT US</div>
  <div class="about-frame"></div>
  <div class="about-photo" role="img" aria-label="Photo of a team meeting around a table with a laptop"></div>
  <div class="about-text">
    <p class="lead">TRAVOLIN is a one-stop destination for all your IT Management Requirements. We are committed to delivering cutting-edge, simplified IT solutions through our highly skilled team and flexible engagement models. Whether you need support for integration or ongoing operational services, TRAVOLIN has the insight and technical capability to deliver simplified solutions.</p>
    <ul>
      <li><svg><use href="#i-check"/></svg>Our passion, enthusiasm, and value are what make us different from our peers. While there are many businesses providing the same services, what we deliver is unparalleled. Whether services or solutions, we keep standing with our clients through thick and thin.</li>
      <li><svg><use href="#i-check"/></svg>Whether you need support for integration or ongoing operational services, TRAVOLIN has the insight and technical capability to deliver simplified solutions.</li>
      <li><svg><use href="#i-check"/></svg>Being an Australian based organization, we are 100% Customer Focused and provide innovative and flexible IT services and simple solutions that enhance business productivity. We pride ourselves on the flexibility in our approach.</li>
    </ul>
  </div>
  <footer class="slide-footer">
    <span class="url">https://www.travolin.com.au/</span><span class="sep"></span>
    <span class="social" style="left:281px"></span><span class="social" style="left:308px"></span><span class="social" style="left:335px"></span>
    <span class="page-no">2</span>
  </footer>
</section>

<!-- Slide 3: What We Offer -->
<section class="slide" style="top:1403px">
  <svg class="header-band" viewBox="0 0 1048 82"><polygon points="346,0 1048,0 1048,82 428,82" fill="url(#band-grad)"/></svg>
  <div class="logo">travolin</div>
  <div class="slide-title">WHAT WE OFFER</div>
  <p class="slide-intro" style="top:118px">The world of technology can be fast-paced and scary. That's why our goal is to provide an experience that is tailored to your company's needs. No matter the budget, we pride ourselves on providing professional customer service</p>
  <div class="offer-grid">
    <div class="offer-card"><div class="icon-tile"><svg><use href="#i-shield"/></svg></div><span>Managed Antivirus</span></div>
    <div class="offer-card"><div class="icon-tile"><svg><use href="#i-server"/></svg></div><span>Server &amp; Network Support</span></div>
    <div class="offer-card"><div class="icon-tile"><svg><use href="#i-gear"/></svg></div><span>Desktop &amp; End User Support</span></div>
    <div class="offer-card"><div class="icon-tile"><svg><use href="#i-lock"/></svg></div><span>Cyber Security Support</span></div>
    <div class="offer-card"><div class="icon-tile"><svg><use href="#i-db"/></svg></div><span>Managed Backup &amp; Recovery</span></div>
    <div class="offer-card"><div class="icon-tile"><svg><use href="#i-cloud"/></svg></div><span>Managed Email &amp; Cloud Operations</span></div>
    <div class="offer-card"><div class="icon-tile"><svg><use href="#i-code"/></svg></div><span>Software Development</span></div>
    <div class="offer-card"><div class="icon-tile"><svg><use href="#i-cloud"/></svg></div><span>Application Hosting Services</span></div>
    <div class="offer-card"><div class="icon-tile"><svg><use href="#i-gear"/></svg></div><span>Systems Assurance</span></div>
    <div class="offer-card"><div class="icon-tile"><svg><use href="#i-monitor"/></svg></div><span>IT Consulting</span></div>
    <div class="offer-card"><div class="icon-tile"><svg><use href="#i-gear"/></svg></div><span>Project Services</span></div>
    <div class="offer-card"><div class="icon-tile"><svg><use href="#i-chart"/></svg></div><span>Procurement Services</span></div>
    <div class="offer-card"><div class="icon-tile"><svg><use href="#i-chart"/></svg></div><span>Infrastructure Management Services</span></div>
    <div class="offer-card"><div class="icon-tile"><svg><use href="#i-gear"/></svg></div><span>Automation</span></div>
    <div class="offer-card"><div class="icon-tile"><svg><use href="#i-gear"/></svg></div><span>Field Services</span></div>
    <div class="offer-card"><div class="icon-tile"><svg><use href="#i-monitor"/></svg></div><span>Network Monitoring</span></div>
  </div>
  <footer class="slide-footer">
    <span class="url">https://www.travolin.com.au/</span><span class="sep"></span>
    <span class="social" style="left:281px"></span><span class="social" style="left:308px"></span><span class="social" style="left:335px"></span>
    <span class="page-no">3</span>
  </footer>
</section>

<!-- Slide 4: Managed Service Desk -->
<section class="slide" style="top:2060px">
  <svg class="header-band" viewBox="0 0 1048 82"><polygon points="346,0 1048,0 1048,82 428,82" fill="url(#band-grad)"/></svg>
  <div class="logo">travolin</div>
  <div class="slide-title">MANAGED SERVICE DESK</div>
  <p class="slide-intro" style="top:118px">Single point of contact for incident and service request handling &amp; remote support including a fixed monthly rate with unlimited support under service level agreements through global coverage</p>
  <svg class="desk-diagram" width="1048" height="588" viewBox="0 0 1048 588">
    <g fill="none" stroke="#35b8e8" stroke-width="1.3">
      <circle cx="245" cy="338" r="126" stroke="#5f646b" stroke-width="1.5"/>
      <polyline points="330,247 368,214 437,214"/>
      <polyline points="365,296 437,296"/>
      <polyline points="365,388 437,388"/>
      <polyline points="330,437 368,470 437,470"/>
    </g>
    <g fill="#fff" stroke="#35b8e8" stroke-width="1.5">
      <circle cx="330" cy="247" r="4"/><circle cx="365" cy="296" r="4"/><circle cx="365" cy="388" r="4"/><circle cx="330" cy="437" r="4"/>
    </g>
    <circle cx="245" cy="338" r="112" fill="url(#disc-grad)"/>
    <text x="245" y="352" text-anchor="middle" font-family="Roboto, Arial, sans-serif" font-weight="300" font-size="42" fill="#fff" letter-spacing="1">travolin</text>
    <g>
      <circle cx="465" cy="214" r="28" fill="#fff" stroke="#e1e6ea" stroke-width="3"/>
      <circle cx="465" cy="296" r="28" fill="#fff" stroke="#e1e6ea" stroke-width="3"/>
      <circle cx="465" cy="388" r="28" fill="#fff" stroke="#e1e6ea" stroke-width="3"/>
      <circle cx="465" cy="470" r="28" fill="#fff" stroke="#e1e6ea" stroke-width="3"/>
      <circle cx="465" cy="214" r="16" fill="url(#disc-grad)"/>
      <circle cx="465" cy="296" r="16" fill="url(#disc-grad)"/>
      <circle cx="465" cy="388" r="16" fill="url(#disc-grad)"/>
      <circle cx="465" cy="470" r="16" fill="url(#disc-grad)"/>
      <use href="#i-server" x="455" y="204" width="20" height="20"/>
      <use href="#i-gear" x="455" y="286" width="20" height="20"/>
      <use href="#i-db" x="455" y="378" width="20" height="20"/>
      <use href="#i-globe" x="455" y="460" width="20" height="20"/>
    </g>
  </svg>
  <div class="desk-item" style="top:203px"><h3>SERVER &amp; NETWORK SUPPORT</h3><p>Address issues and bugs of your server and network devices as a remote service</p></div>
  <div class="desk-item" style="top:277px"><h3>DESKTOP &amp; END USER SUPPORT</h3><p>Address technical issues and bugs of your desktop environment as well as your users as a remote service</p></div>
  <div class="desk-item" style="top:370px"><h3>MANAGED BACKUP &amp; RECOVERY</h3><p>Provide a data backup and restore service to protect your information and documents against internal accidents, threats. Including recovery management</p></div>
  <div class="desk-item" style="top:453px"><h3>NETWORK MONITORING</h3><p>Monitor each device that connected to network in 24 x 7 and maintain the high level of availability of services</p></div>
  <footer class="slide-footer">
    <span class="url">https://www.travolin.com.au/</span><span class="sep"></span>
    <span class="social" style="left:281px"></span><span class="social" style="left:308px"></span><span class="social" style="left:335px"></span>
    <span class="page-no">4</span>
  </footer>
</section>

<!-- Slide 5: Software Development -->
<section class="slide" style="top:2718px">
  <svg class="header-band" viewBox="0 0 1048 82"><polygon points="346,0 1048,0 1048,82 428,82" fill="url(#band-grad)"/></svg>
  <div class="logo">travolin</div>
  <div class="slide-title">SOFTWARE DEVELOPMENT</div>
  <p class="slide-intro" style="top:120px">Builds innovative enterprise systems, software solutions and automation solutions with managed support services</p>
  <article class="dev-card" style="left:61px">
    <div class="dev-icon"><svg><use href="#i-cart"/></svg></div>
    <h3>E-Commance Application<br>Devlopmets</h3>
    <p>Customize E-commerce facilities to make sure your business growth</p>
  </article>
  <article class="dev-card" style="left:380px">
    <div class="dev-icon"><svg><use href="#i-monitor"/></svg></div>
    <h3>Design<br>Websites</h3>
    <p>Provide an attractive UI Design in the latest technology for your personal or commercial website to grow your business. All UI designs and backends are secured from vulnerabilities by our security team</p>
  </article>
  <article class="dev-card" style="left:699px">
    <div class="dev-icon"><svg><use href="#i-code"/></svg></div>
    <h3>Applicaion Hosting<br>Services</h3>
    <p>Introducing a single package for your web sites including standard security, reliable hosting service with 24x7 intelligent monitoring system &amp; smart friendly technical supports</p>
  </article>
  <footer class="slide-footer">
    <span class="url">https://www.travolin.com.au/</span><span class="sep"></span>
    <span class="social" style="left:281px"></span><span class="social" style="left:308px"></span><span class="social" style="left:335px"></span>
    <span class="page-no">5</span>
  </footer>
</section>

<!-- Slide 6: Contact Us -->
<section class="slide contact" style="top:3375px" role="img" aria-label="Contact slide over a faint world map in blue tones">
  <svg class="title-band" width="1048" height="82" viewBox="0 0 1048 82"><polygon points="346,0 1048,0 1048,82 428,82" fill="#fff"/></svg>
  <div class="logo light">travolin</div>
  <div class="slide-title">CONTACT US</div>

  <div class="contact-card main" style="left:79px;top:145px">
    <span class="pin"><svg><use href="#i-pin"/></svg></span>
    <h4>Australia</h4>
    <p>ABN 00 111 222 333 PO BOX 210 HARBOUR VALE 1500<br>NSW AUSTRALIA</p>
    <div class="line" style="color:#35b8e8"><svg><use href="#i-phone"/></svg><span style="color:#333a40">+61 (02) 5550 0142</span></div>
    <div class="line" style="color:#35b8e8"><svg><use href="#i-mail"/></svg><span style="color:#333a40">connect@travolin.com.au</span></div>
  </div>
  <div class="contact-card" style="left:381px;top:145px">
    <span class="pin"><svg><use href="#i-pin"/></svg></span>
    <h4>Sri Lanka</h4>
    <p>12/4A, LOTUS HOUSE 3RD FLOOR,<br>GALLE ROAD 00300, COLOMBO SRI LANKA</p>
    <div class="line" style="color:#fff"><svg><use href="#i-phone"/></svg>+94 11 5550 218</div>
    <div class="line" style="color:#fff"><svg><use href="#i-mail"/></svg>connect@travolin.lk</div>
  </div>
  <div class="contact-card" style="left:686px;top:145px">
    <span class="pin"><svg><use href="#i-pin"/></svg></span>
    <h4>New Zealand</h4>
    <p>18/42 KAURI STREET Riverside<br>Hamilton NZ 3200 NEW ZEALAND</p>
    <div class="line" style="color:#fff"><svg><use href="#i-phone"/></svg>+64 (09) 555 0176</div>
    <div class="line" style="color:#fff"><svg><use href="#i-mail"/></svg>connect@travolin.com.au</div>
  </div>
  <div class="contact-card" style="left:231px;top:333px">
    <span class="pin"><svg><use href="#i-pin"/></svg></span>
    <h4>United States of America</h4>
    <p>465, Lorem ipsum dolor sit amet, consectetur sedea,<br>Sed ut perspiciatis, USA</p>
    <div class="line" style="color:#fff"><svg><use href="#i-phone"/></svg>+1 (555) 0143 2260</div>
    <div class="line" style="color:#fff"><svg><use href="#i-mail"/></svg>connect@travolin.com.us</div>
  </div>
  <div class="contact-card" style="left:534px;top:333px">
    <span class="pin"><svg><use href="#i-pin"/></svg></span>
    <h4>Singapore</h4>
    <p>465, Lorem ipsum dolor sit amet, consectetur sedea,<br>Sed ut perspiciatis, SINGAPORE</p>
    <div class="line" style="color:#fff"><svg><use href="#i-phone"/></svg>+65 5550 3184</div>
    <div class="line" style="color:#fff"><svg><use href="#i-mail"/></svg>connect@travolin.com.sg</div>
  </div>

  <footer class="slide-footer">
    <span class="url">https://www.travolin.com.au/</span><span class="sep"></span>
    <span class="social" style="left:281px"></span><span class="social" style="left:308px"></span><span class="social" style="left:335px"></span>
    <span class="page-no">6</span>
  </footer>
</section>

</body>
</html>
```